Book Cover for Lantern Cousins Notes from the Orchard

We have written a book that brings together Notes from the Orchard from a variety of women's voices.
We developed a draft book cover that we like using Canva (attached below). We'd love a book cover that is similar to this image, but looks more professional.
Following are the themes we’d like to depict in the book cover, and in parentheses, how they are represented in the current cover:
1. Divinely feminine (overall cover)
2. Currents of enlightenment (the swirls of light carrying the butterfly)
3. Diversity (a myriad of colors)
4. The solo journey into the unknown (the single butterfly’s flight)
5. Buoyancy and joy (again, the dancing colors and floating butterfly)
6. Boldly feminine (the blue butterfly, set against brush strokes of light)
7. Homage to a dear friend (she loved blue butterflies, the cosmos - this butterfly has hints of the cosmos in her wings, and painting - this background has brush strokes of light).
Book Title, Subtitle, and Editor:
Lantern Cousins
Notes from the Orchard
Edited by Ilse Varno
Thank you very much for considering this project!
People who are interested in Women and Spirituality

```html
<!DOCTYPE html>
<html lang="en">
<head>
<meta charset="utf-8">
<title>Lantern Cousins — Notes from the Orchard</title>
<link rel="stylesheet" href="https://fonts.googleapis.com/css2?family=Alegreya+Sans:wght@400;500&family=Parisienne&display=swap">
<style>
  :root {
    --plum: #7c3950;
    --cover-top: #fde8e0;
    --cover-mid: #fdf1db;
    --cover-lower: #f7c6a6;
    --cover-bottom: #ee9290;
    --title-pink: #d9538a;
    --ink: #1c1416;
    --wing-light: rgba(63, 183, 220, 0.9);
    --wing-mid: rgba(42, 134, 207, 0.7);
    --wing-deep: rgba(31, 79, 176, 0.35);
    --glow: rgba(240, 140, 110, 0.45);
  }
  html, body {
    margin: 0;
    width: 1200px;
    height: 1200px;
    overflow: hidden;
    background: var(--plum);
  }
  .stage {
    position: relative;
    width: 1200px;
    height: 1200px;
  }
  .cover {
    position: absolute;
    left: 250px;
    top: 50px;
    width: 700px;
    height: 1100px;
    background:
      radial-gradient(ellipse 120px 30px at 505px 825px, var(--glow) 0%, rgba(240,140,110,0) 100%),
      linear-gradient(180deg, var(--cover-top) 0%, var(--cover-mid) 30%, var(--cover-mid) 45%, var(--cover-lower) 78%, var(--cover-bottom) 100%);
    overflow: hidden;
  }
  .cover__title {
    position: absolute;
    top: 70px;
    left: 0;
    right: 0;
    margin: 0;
    text-align: center;
    font-family: "Alegreya Sans", sans-serif;
    font-weight: 400;
    font-size: 80px;
    letter-spacing: 1px;
    color: var(--title-pink);
    line-height: 1;
  }
  .cover__subtitle {
    position: absolute;
    top: 176px;
    left: 0;
    right: 0;
    margin: 0;
    text-align: center;
    font-family: "Parisienne", cursive;
    font-weight: 400;
    font-size: 42px;
    color: var(--ink);
    line-height: 1;
  }
  .cover__art {
    position: absolute;
    left: 340px;
    top: 440px;
    width: 280px;
    height: 380px;
    background: radial-gradient(closest-side, var(--wing-light) 0%, var(--wing-mid) 45%, var(--wing-deep) 75%, rgba(31,79,176,0) 100%);
  }
  .cover__editor {
    position: absolute;
    top: 975px;
    left: 0;
    right: 0;
    margin: 0;
    text-align: center;
    font-family: "Alegreya Sans", sans-serif;
    font-weight: 500;
    font-size: 34px;
    letter-spacing: 1.5px;
    color: var(--ink);
    line-height: 1;
  }
</style>
</head>
<body>
  <main class="stage">
    <section class="cover">
      <h1 class="cover__title">Lantern Cousins</h1>
      <p class="cover__subtitle">Notes from the Orchard</p>
      <div class="cover__art" role="img" aria-label="A single blue butterfly with iridescent wings, perched in profile"></div>
      <p class="cover__editor">Edited by Ilse Varno</p>
    </section>
  </main>
</body>
</html>
```